Novexa company website, a website for employment for people with autism

The website will make a match between people and jobs, mainly in the graphical sector, but also other sectors.
The name of the company is novexa and automates jobs with people that are on the autism spectrum.
The whole matchmaking and feedback process and so doesn't have to be in this prototype, we just want the general information pages and to convey a great look and brand identity that we will keep in the other pages to be developed. The website must be made with Wordpress, since the backend will be developed in Wordpress too.
It is a social project that wants to create possibilites for people with ASS to work from home for an employer or to do a variety of tasks for different customers.
The people we hire are generally not on the regular job market or have difficulty finding a job and "selling themselves"

Target Market(s)

matchmaking between talent (with ASS) and employers / jobs

Number of Pages Required

5+ page

Font styles to use
Sans Serif

Colors
ec1f27
e34298
a64599
6b449b
0355a3
0792cd

Requirements
Must have
• A stunning landing pages
• Integrate our logo and must match with what will do. We want a clean, modern, minimalistic, sleek website that radiates creativity and good looks.
• We have one page describing what we can do for customers, one page for people with ASS that would like to be candidates (our approach, learning program, ...), two pages that are addressed to partners who want to cooperate: the one's that can assist with autism related assistance and the one's that can help with the job coaching.
Nice to have
• In our logo are many colors as we embrace diversity and want to show that. Out main branding colors are red (for action) and blue for stability and will all gradients that go with it. Mainly white or black (or anthracite) for other parts
Should not have
• We want a modern and minimalistic design, no fluffy designs with lots of ornaments.

```html
<!DOCTYPE html>
<html lang="en">
<head>
<meta charset="utf-8">
<title>Novexa – Automates Jobs</title>
<link rel="stylesheet" href="https://fonts.googleapis.com/css2?family=Raleway:wght@500;600;700&family=Open+Sans:wght@400;600;700&family=Roboto:wght@400;500&display=swap">
<style>
:root{
  --red:#ec1f27;
  --pink:#e34298;
  --magenta:#a64599;
  --purple:#6b449b;
  --navy:#0355a3;
  --sky:#0792cd;
  --hex-blue:#1d80c3;
  --ink:#222428;
  --text:#555a60;
  --line:#d9dbe0;
  --white:#ffffff;
  --black:#000000;
  --star:#f5b731;
}
*{box-sizing:border-box;margin:0;padding:0}
html,body{width:1200px;height:3982px;overflow:hidden}
body{position:relative;background:var(--white);font-family:"Open Sans",Arial,sans-serif;color:var(--ink)}
.abs{position:absolute}
a{color:inherit;text-decoration:none}

/* hero */
.hero{left:0;top:0;width:1200px;height:590px;background:radial-gradient(ellipse at 50% 45%,#2d6f86 0%,#15495c 40%,#0b2c3b 80%,#071f2b 100%)}
.hero-art{left:430px;top:90px;width:300px;height:330px;border-radius:40% 40% 30% 30%;background:radial-gradient(ellipse at 50% 40%,rgba(190,120,220,.75),rgba(60,140,190,.35) 55%,rgba(0,0,0,0) 75%)}
.brand{left:88px;top:20px;width:180px;text-align:center;color:var(--white);font-family:"Raleway",sans-serif;font-weight:600;font-size:25px;letter-spacing:3px}
.brand-dot{display:block;width:44px;height:44px;border-radius:50%;background:var(--magenta);margin:0 auto 8px}
.top-phone{left:735px;top:31px;color:var(--white);font-family:"Roboto",sans-serif;font-size:17px;display:flex;align-items:center;gap:6px}
.btn-register{left:911px;top:29px;width:114px;height:31px;border:2px solid var(--white);color:var(--white);font-size:16px;font-family:"Roboto",sans-serif;display:flex;align-items:center;justify-content:center}
.btn-login{left:1035px;top:29px;width:75px;height:31px;background:var(--purple);color:var(--white);font-size:16px;font-family:"Roboto",sans-serif;display:flex;align-items:center;justify-content:center}
.main-nav{top:82px;left:0;width:1200px;height:24px;font-family:"Roboto",sans-serif;font-size:17px;color:var(--white)}
.main-nav a{position:absolute;top:0}
.play{left:570px;top:204px;width:60px;height:60px}
.hero-title{left:0;top:270px;width:1200px;text-align:center;color:var(--white);font-family:"Roboto",sans-serif;font-weight:500;font-size:74px}
.hero-sub{left:0;top:360px;width:1200px;text-align:center;color:var(--white);font-family:"Roboto",sans-serif;font-size:42px}
.hero-arrows{left:100px;top:506px;width:60px;height:24px}

/* search */
.search{left:0;top:590px;width:1200px;height:100px;background:linear-gradient(90deg,var(--purple),#7d4598 60%,var(--purple))}
.select{top:616px;width:255px;height:56px;background:var(--white);font-size:16px;color:var(--text);padding:0 18px;display:flex;align-items:center;justify-content:space-between}
.select::after{content:"";border:6px solid transparent;border-top:7px solid #333;margin-top:6px}
.btn-find{left:911px;top:614px;width:140px;height:56px;background:var(--pink);color:var(--white);font-size:21px;font-weight:600;display:flex;align-items:center;justify-content:center}

/* features */
.section-title{left:0;width:1200px;text-align:center;font-family:"Raleway",sans-serif;font-weight:700;color:var(--ink)}
.feature{top:974px;width:308px;height:290px;border:1px solid var(--line);background:var(--white);text-align:center}
.feature.is-active{box-shadow:0 4px 18px rgba(0,0,0,.18);border-color:#e3e3e6}
.feature h3{position:absolute;top:84px;left:0;width:100%;font-size:20px;font-weight:700;color:var(--ink)}
.feature p{position:absolute;top:124px;left:38px;width:232px;font-size:13.5px;line-height:23px;color:var(--text)}
.pill{position:absolute;left:100px;top:222px;width:108px;height:34px;border:1.5px solid #777;border-radius:17px;font-size:14px;color:#444;display:flex;align-items:center;justify-content:center}
.pill.is-filled{background:var(--magenta);border-color:var(--magenta);color:var(--white)}
.hex{top:916px;width:112px;height:124px}

/* about */
.about{left:0;top:1368px;width:1200px;height:562px;background:linear-gradient(100deg,var(--navy) 0%,#2e5fa8 40%,#5a4ca0 70%,var(--purple) 85%,#7e4597 100%)}
.about-frame{left:96px;top:1474px;width:420px;height:318px;border:2px solid rgba(255,255,255,.85)}
.about-photo{left:125px;top:1505px;width:438px;height:327px;background:linear-gradient(120deg,#3a2d25,#6b5443 45%,#2a3a4c 100%)}
.about-title{left:605px;top:1505px;color:var(--white);font-family:"Raleway",sans-serif;font-weight:500;font-size:52px}
.about-text{left:605px;top:1582px;width:505px;color:var(--white);font-size:14.5px;line-height:26.5px}
.btn-red{left:605px;top:1788px;width:122px;height:34px;background:var(--red);color:var(--white);font-size:16px;display:flex;align-items:center;justify-content:center}

/* jobs */
.job{top:2169px;width:319px;height:393px;background:var(--white);box-shadow:0 3px 14px rgba(0,0,0,.2);text-align:center}
.job-photo{width:100%;height:199px}
.job time{position:absolute;top:228px;left:0;width:100%;font-size:12.5px;color:var(--navy)}
.job h4{position:absolute;top:255px;left:0;width:100%;font-size:16px;font-weight:400;color:var(--ink)}
.job p{position:absolute;top:292px;left:42px;width:236px;font-size:12.5px;line-height:20px;color:var(--text);height:40px;overflow:hidden}
.job .more{position:absolute;top:348px;left:0;width:100%;font-size:13.5px;color:var(--navy)}
.dots{left:576px;top:2624px;width:48px;height:14px;display:flex;gap:6px}
.dots i{width:10px;height:10px;border-radius:50%;background:#8d96a6}
.dots i:first-child{background:var(--navy)}

/* cta */
.cta{left:0;top:2727px;width:1200px;height:300px;background:linear-gradient(100deg,#8e3f95 0%,var(--purple) 35%,#3a5aa8 70%,var(--sky) 100%)}
.cta h2{position:absolute;top:72px;left:0;width:100%;text-align:center;color:var(--white);font-family:"Raleway",sans-serif;font-weight:700;font-size:45px}
.cta p{position:absolute;top:132px;left:0;width:100%;text-align:center;color:var(--white);font-size:19px}
.btn-ghost{left:512px;top:2915px;width:176px;height:51px;border:2px solid var(--white);color:var(--white);font-size:24px;display:flex;align-items:center;justify-content:center}

/* testimonial */
.quote-mark{left:158px;top:3122px;width:60px;height:48px}
.testi-title{left:158px;top:3186px;font-family:"Raleway",sans-serif;font-weight:500;font-size:50px;color:var(--ink)}
.testi-text{left:158px;top:3262px;width:540px;font-size:15px;line-height:31px;color:var(--text)}
.testi-name{left:158px;top:3390px;font-size:18px;color:var(--navy);font-weight:600}
.stars{left:158px;top:3435px;width:150px;height:28px}
.testi-ring{left:740px;top:3140px;width:320px;height:320px;border-radius:50%;border:2px solid var(--sky)}
.testi-photo{left:752px;top:3152px;width:296px;height:296px;border-radius:50%;background:radial-gradient(circle at 50% 40%,#c89a80,#8a6a5a 55%,#d8d4d0 100%)}
.arrow-btn{top:3262px;width:56px;height:56px}

/* footer */
.footer{left:0;top:3571px;width:1200px;height:411px;background:var(--black);color:var(--white)}
.footer-brand{left:112px;top:3690px;width:180px;text-align:center;font-family:"Raleway",sans-serif;font-weight:600;font-size:25px;letter-spacing:3px;color:var(--white)}
.footer h5{position:absolute;font-size:17px;font-weight:600;color:var(--white)}
.contact-item{left:393px;display:flex;gap:14px;font-size:13.5px;line-height:20px;color:var(--white)}
.contact-item svg{flex:none;margin-top:2px}
.quick{left:735px;top:3695px;font-size:13.5px;line-height:25px;list-style:none;color:var(--white)}
.quick li::before{content:"›";margin-right:10px}
.social{left:958px;display:flex;align-items:center;gap:12px;font-size:15px;color:var(--white)}
.social i{width:26px;height:26px;border-radius:50%;border:1.5px solid var(--white)}
.copyright{left:0;top:3926px;width:1200px;text-align:center;font-size:13.5px;color:var(--white)}
</style>
</head>
<body>

<header>
  <div class="abs hero" role="img" aria-label="Photo of a colourful smoke plume on a dark teal background"></div>
  <div class="abs hero-art" aria-hidden="true"></div>
  <div class="abs brand"><span class="brand-dot"></span>NOVEXA</div>
  <div class="abs top-phone">
    <svg width="16" height="16" viewBox="0 0 24 24"><path fill="#fff" d="M6.6 10.8a15 15 0 0 0 6.6 6.6l2.2-2.2c.3-.3.7-.4 1-.2 1.1.4 2.3.6 3.6.6.6 0 1 .4 1 1V20c0 .6-.4 1-1 1A17 17 0 0 1 3 4c0-.6.4-1 1-1h3.5c.6 0 1 .4 1 1 0 1.3.2 2.5.6 3.6.1.3 0 .7-.2 1z"/></svg>
    +1 555-010-2030
  </div>
  <a class="abs btn-register">Registered</a>
  <a class="abs btn-login">Login</a>
  <nav class="abs main-nav">
    <a style="left:610px">Home</a>
    <a style="left:708px">About us</a>
    <a style="left:830px">Job</a>
    <a style="left:910px">Novexa</a>
    <a style="left:1040px">Contacts</a>
  </nav>
  <svg class="abs play" viewBox="0 0 60 60"><circle cx="30" cy="30" r="29" fill="#1a1a1a"/><path d="M24 18l18 12-18 12z" fill="#fff"/></svg>
  <h1 class="abs hero-title">Automates Jobs</h1>
  <p class="abs hero-sub">Neque porro quisquam dolorem ipsum</p>
  <svg class="abs hero-arrows" viewBox="0 0 60 24"><path d="M14 5l-7 7 7 7M46 5l7 7-7 7" stroke="#fff" stroke-width="2" fill="none"/></svg>
</header>

<section class="abs search" aria-label="Job search"></section>
<div class="abs select" style="left:98px">Job tile</div>
<div class="abs select" style="left:372px">Skill</div>
<div class="abs select" style="left:642px">City or state</div>
<a class="abs btn-find">Find job</a>

<h2 class="abs section-title" style="top:815px;font-size:43px">Why People Choose Us</h2>

<article class="abs feature" style="left:112px">
  <h3>VERIFIED EMPLOYERS</h3>
  <p>It is a long established fact that a reader will be distracted by the readable content of a page</p>
  <a class="pill">Read more</a>
</article>
<article class="abs feature is-active" style="left:449px">
  <h3>DEMANDED VACANCIES</h3>
  <p>It is a long established fact that a reader will be distracted by the readable content of a page</p>
  <a class="pill is-filled">Read more</a>
</article>
<article class="abs feature" style="left:789px">
  <h3>EMPLOYMENT BLOG</h3>
  <p>It is a long established fact that a reader will be distracted by the readable content of a page</p>
  <a class="pill">Read more</a>
</article>

<svg class="abs hex" style="left:210px" viewBox="0 0 112 124"><path d="M56 2l52 30v60l-52 30L4 92V32z" fill="var(--hex-blue)"/><circle cx="52" cy="58" r="15" fill="none" stroke="#fff" stroke-width="6"/><path d="M62 68l14 14" stroke="#fff" stroke-width="8" stroke-linecap="round"/></svg>
<svg class="abs hex" style="left:547px" viewBox="0 0 112 124"><path d="M56 2l52 30v60l-52 30L4 92V32z" fill="var(--magenta)"/><circle cx="56" cy="62" r="22" fill="#fff"/><path d="M45 62l8 8 14-15" stroke="var(--magenta)" stroke-width="6" fill="none"/></svg>
<svg class="abs hex" style="left:886px" viewBox="0 0 112 124"><path d="M56 2l52 30v60l-52 30L4 92V32z" fill="var(--hex-blue)"/><ellipse cx="50" cy="56" rx="20" ry="14" fill="#fff"/><path d="M38 66l-6 10 14-6z" fill="#fff"/><ellipse cx="66" cy="70" rx="18" ry="12" fill="#fff" stroke="var(--hex-blue)" stroke-width="3"/><path d="M76 78l6 9-13-5z" fill="#fff"/></svg>

<section class="abs about" aria-label="About us"></section>
<div class="abs about-frame"></div>
<div class="abs about-photo" role="img" aria-label="Photo of a person working on a laptop at a wooden desk"></div>
<svg class="abs play" style="left:318px;top:1640px" viewBox="0 0 60 60"><circle cx="30" cy="30" r="29" fill="#1a1a1a"/><path d="M24 18l18 12-18 12z" fill="#fff"/></svg>
<h2 class="abs about-title">ABOUT US</h2>
<p class="abs about-text">It is a long established fact that a reader will be distracted by the readable content of a page when looking at its layout. The point of using Lorem Ipsum is that it has a more-or-less normal distribution of letters, as opposed to using 'Content here, content here', making it look like readable English. Many desktop publishing packages and web page editors now use Lorem Ipsum as their default model text, and a search for 'lorem ipsum' will uncover many web sites still in their infancy</p>
<a class="abs btn-red">Read More</a>

<h2 class="abs section-title" style="top:2052px;font-size:48px">Automates Jobs</h2>

<article class="abs job" style="left:93px">
  <div class="job-photo" role="img" aria-label="Photo of a barista serving a customer at a counter" style="background:linear-gradient(135deg,#b98a66,#d9c0a4 50%,#8e5a3c)"></div>
  <time>August 31, 2019</time>
  <h4>Porro quisquam est dolorem</h4>
  <p>The point of using Lorem Ipsum is that it has a more-or-less normal distribution of letters</p>
  <a class="more">Read More »</a>
</article>
<article class="abs job" style="left:433px">
  <div class="job-photo" role="img" aria-label="Photo of a man in a suit working at a laptop" style="background:linear-gradient(135deg,#4d5a3a,#2a2e3a 50%,#6d6a5a)"></div>
  <time>August 31, 2019</time>
  <h4>Ipsum quia dolor sit amet</h4>
  <p>The point of using Lorem Ipsum is that it has a more-or-less normal distribution of letters</p>
  <a class="more">Read More »</a>
</article>
<article class="abs job" style="left:770px">
  <div class="job-photo" role="img" aria-label="Photo of two young people studying together" style="background:linear-gradient(135deg,#c8c4bc,#b04a44 55%,#6a6e78)"></div>
  <time>August 31, 2019</time>
  <h4>Dolorem ipsum quia dolor</h4>
  <p>The point of using Lorem Ipsum is that it has a more-or-less normal distribution of letters</p>
  <a class="more">Read More »</a>
</article>
<div class="abs dots"><i></i><i></i><i></i></div>

<section class="abs cta" aria-label="Call to action">
  <h2>Save time by finding the right employer</h2>
  <p>Over 1 million interactions, 50,000 success stories Make yours now.</p>
</section>
<a class="abs btn-ghost">Click Here</a>

<svg class="abs quote-mark" viewBox="0 0 60 48"><path d="M2 46V24C2 10 10 3 24 2v8c-7 1-10 5-10 12h10v24zM34 46V24c0-14 8-21 22-22v8c-7 1-10 5-10 12h10v24z" fill="var(--navy)"/></svg>
<h2 class="abs testi-title">Testimonial</h2>
<p class="abs testi-text">"It is a long established fact that a reader will be distracted by the readable content of a page when looking at its layout. The point of using Lorem Ipsum is that it has a more-or-less normal distribution of letters, as opposed to using 'Content here, content here', making it look like "</p>
<p class="abs testi-name">Alex Carter Cloud Engineer</p>
<svg class="abs stars" viewBox="0 0 150 28">
  <g fill="var(--star)">
    <path id="st" d="M12 1l3.4 7 7.6 1-5.5 5.3 1.3 7.6L12 18.3 5.2 21.9l1.3-7.6L1 9l7.6-1z"/>
    <use href="#st" x="28"/><use href="#st" x="56"/><use href="#st" x="84"/><use href="#st" x="112"/>
  </g>
</svg>
<div class="abs testi-ring"></div>
<div class="abs testi-photo" role="img" aria-label="Portrait photo of a smiling young woman"></div>
<svg class="abs arrow-btn" style="left:54px" viewBox="0 0 56 56"><circle cx="28" cy="28" r="27" fill="#fff" stroke="#c9ccd2"/><path d="M32 19l-9 9 9 9" stroke="#444" stroke-width="2" fill="none"/></svg>
<svg class="abs arrow-btn" style="left:1087px" viewBox="0 0 56 56"><circle cx="28" cy="28" r="27" fill="#fff" stroke="#c9ccd2"/><path d="M24 19l9 9-9 9" stroke="#444" stroke-width="2" fill="none"/></svg>

<footer class="abs footer">
  <h5 style="left:393px;top:68px">CONTACT US</h5>
  <h5 style="left:735px;top:68px">QUICK LINKS</h5>
  <h5 style="left:958px;top:68px">FOLLOW US</h5>
</footer>
<div class="abs footer-brand"><span class="brand-dot"></span>NOVEXA</div>
<div class="abs contact-item" style="top:3695px">
  <svg width="16" height="20" viewBox="0 0 16 20"><path d="M8 0a7 7 0 0 0-7 7c0 5 7 13 7 13s7-8 7-13a7 7 0 0 0-7-7zm0 10a3 3 0 1 1 0-6 3 3 0 0 1 0 6z" fill="#fff"/></svg>
  <span>210 Harbor Lane 4th Floor<br>Springfield, ST 20410</span>
</div>
<div class="abs contact-item" style="top:3755px">
  <svg width="16" height="16" viewBox="0 0 24 24"><path fill="#fff" d="M6.6 10.8a15 15 0 0 0 6.6 6.6l2.2-2.2c.3-.3.7-.4 1-.2 1.1.4 2.3.6 3.6.6.6 0 1 .4 1 1V20c0 .6-.4 1-1 1A17 17 0 0 1 3 4c0-.6.4-1 1-1h3.5c.6 0 1 .4 1 1 0 1.3.2 2.5.6 3.6.1.3 0 .7-.2 1z"/></svg>
  <span>555-014-7788</span>
</div>
<div class="abs contact-item" style="top:3792px">
  <svg width="16" height="14" viewBox="0 0 16 14"><rect x="0" y="1" width="16" height="12" fill="#fff"/><path d="M0 1l8 6 8-6" stroke="#000" stroke-width="1.5" fill="none"/></svg>
  <span>info@novexa-mail.com</span>
</div>
<ul class="abs quick">
  <li>Home</li><li>About Us</li><li>Job</li><li>News</li><li>Contact Us</li>
</ul>
<div class="abs social" style="top:3700px"><i></i>Friendly</div>
<div class="abs social" style="top:3746px"><i></i>Shotbox</div>
<div class="abs social" style="top:3792px"><i></i>Circleup</div>
<p class="abs copyright">© Copyright 2019 . All Rights Reserved.</p>

</body>
</html>
```